Business card for a Exhibition booth fabrication company

Hi. My company would like to change our corporate name card. We are an events and Exhibition stand builder company. We would like our corporate name card to resonate what we do. I need someone to create something unique that relates to the industry that I am in. The graphic designer should be creative to incorporate the elements of my industry and try to blend in well in the design of the card. Our aim is to ensure that we are unique and our card can look different from our competitors.
Updates

Target Market(s)

Marketing and events manager from all companies

Contact Information for Business Card

The business card should have the following details:
Name
Job Title
Email
Website

Colors

Designer to choose colors to be used in the design.

Requirements
Must have
• The card must be look something that is relevant to the service that I am providing. My website is: www.velmora-buildworks.com
• You can see my website to get more information on what service that I am doing
Nice to have
• On the back of my card, I would like to have a globe image with the incorporation of my company logo. This is to indicate that my services can be done in any part of the world.

```html
<!DOCTYPE html>
<html lang="en">
<head>
<meta charset="utf-8">
<title>Velmora Buildworks — Business Card</title>
<link href="https://fonts.googleapis.com/css2?family=Montserrat:wght@500;600&family=Noto+Serif:wght@400&display=swap" rel="stylesheet">
<style>
  :root {
    --backdrop: #8e8e8e;
    --paper: #ffffff;
    --charcoal: #2f2f30;
    --charcoal-edge: #5a5455;
    --brand-red: #e11f26;
    --brand-red-dark: #a9161b;
    --ink: #333333;
    --map-grey: #d9d9d9;
  }
  * { box-sizing: border-box; margin: 0; padding: 0; }
  html, body { width: 1200px; height: 1200px; overflow: hidden; }
  body { background: var(--backdrop); position: relative; font-family: "Noto Serif", serif; }

  .card {
    position: absolute;
    background: var(--paper);
    overflow: hidden;
    box-shadow: 0 10px 26px rgba(0,0,0,0.28);
  }

  /* Front (portrait) */
  .card-front { left: 70px; top: 270px; width: 380px; height: 660px; }
  .front-shapes { position: absolute; inset: 0; }
  .name-ribbon {
    position: absolute; left: 0; top: 40px; width: 100%; height: 86px;
    padding: 14px 28px; color: #fff;
  }
  .person-name {
    font-family: "Montserrat", sans-serif; font-weight: 500;
    font-size: 30px; letter-spacing: 0.5px; line-height: 1;
  }
  .person-name .surname { color: rgba(255,255,255,0.55); }
  .person-title { font-size: 15px; margin-top: 8px; }

  .brand-lockup {
    position: absolute; left: 0; top: 205px; width: 100%;
    display: flex; align-items: center; justify-content: center; gap: 12px;
  }
  .brand-dot { width: 18px; height: 18px; border-radius: 50%; background: var(--brand-red); }
  .brand-name {
    font-family: "Montserrat", sans-serif; font-weight: 600;
    font-size: 21px; letter-spacing: 2px; color: var(--ink); text-transform: uppercase;
  }

  .contact-list {
    position: absolute; left: 40px; top: 410px; list-style: none;
    color: #fff; font-size: 16px;
  }
  .contact-list li { display: flex; align-items: center; gap: 12px; margin-bottom: 14px; }
  .contact-list svg { width: 16px; height: 16px; flex: none; }

  .address-band {
    position: absolute; left: 0; bottom: 34px; width: 100%; height: 68px;
    background: var(--brand-red); color: #fff;
    padding: 12px 28px; font-size: 15px; line-height: 1.45;
  }

  /* Back (landscape) */
  .card-back { left: 500px; top: 420px; width: 630px; height: 360px; }
  .world-map {
    position: absolute; left: 90px; top: 30px; width: 460px; height: 300px;
    border-radius: 50%;
    background: radial-gradient(ellipse at 55% 45%, #c9c9c9 0%, var(--map-grey) 45%, rgba(255,255,255,0) 72%);
  }
  .back-lockup {
    position: absolute; inset: 0;
    display: flex; align-items: center; justify-content: center; gap: 16px;
  }
  .back-lockup .brand-dot { width: 26px; height: 26px; }
  .back-lockup .brand-name { font-size: 32px; letter-spacing: 3px; }
</style>
</head>
<body>

  <section class="card card-front" aria-label="Business card front">
    <svg class="front-shapes" viewBox="0 0 380 660" preserveAspectRatio="none" aria-hidden="true">
      <rect width="380" height="660" fill="var(--paper)"/>
      <rect x="0" y="40" width="380" height="86" fill="var(--brand-red)"/>
      <polygon points="300,126 380,126 380,150" fill="var(--brand-red-dark)"/>
      <polygon points="0,400 380,318 380,330 0,412" fill="var(--charcoal-edge)"/>
      <polygon points="0,412 380,330 380,660 0,660" fill="var(--charcoal)"/>
      <polygon points="250,345 330,328 320,352" fill="var(--brand-red)"/>
    </svg>

    <div class="name-ribbon">
      <p class="person-name">DARA <span class="surname">QUILL</span></p>
      <p class="person-title">Director</p>
    </div>

    <div class="brand-lockup">
      <span class="brand-dot"></span>
      <span class="brand-name">Velmora Buildworks</span>
    </div>

    <ul class="contact-list">
      <li>
        <svg viewBox="0 0 16 16"><path d="M4 1l3 3-2 2c1 2 3 4 5 5l2-2 3 3-2 2C7 14 2 9 2 3z" fill="var(--brand-red)"/></svg>
        (123) 555-0148
      </li>
      <li>
        <svg viewBox="0 0 16 16"><rect x="1" y="3" width="14" height="10" fill="var(--brand-red)"/><path d="M1 3l7 6 7-6" stroke="#fff" stroke-width="1.4" fill="none"/></svg>
        username@velmora-buildworks.com
      </li>
      <li>
        <svg viewBox="0 0 16 16"><circle cx="8" cy="8" r="7" fill="var(--brand-red)"/><path d="M1 8h14M8 1v14M3 4h10M3 12h10" stroke="#fff" stroke-width="1"/></svg>
        www.velmora-buildworks.com
      </li>
    </ul>

    <div class="address-band">
      4820 Harbor Lane 210<br>Austin, TX 73301
    </div>
  </section>

  <section class="card card-back" aria-label="Business card back">
    <div class="world-map" role="img" aria-label="Faint grey world map behind the company name"></div>
    <div class="back-lockup">
      <span class="brand-dot"></span>
      <span class="brand-name">Velmora Buildworks</span>
    </div>
  </section>

</body>
</html>
```